Business card for a new cabinet shop company named Veloran Cabinets for high end cabinets

Design a business card, thinking dark rich green with colours to speak of high end luxury ie; cream, gold, black possibly

Mitchell Tarrowby
Director Craftsman
Email: info@veloranjoinery-example.com.au
Instagram : @veloran.cabinets

```html
<!DOCTYPE html>
<html lang="en">
<head>
<meta charset="utf-8">
<title>Veloran Cabinets – Business Card</title>
<link rel="stylesheet" href="https://fonts.googleapis.com/css2?family=Montserrat:wght@400;500;700&display=swap">
<style>
  :root {
    --backdrop: #e4e6e5;
    --card-deep: #17241f;
    --card-mid: #26342f;
    --card-light: #3b4945;
    --gold: #c29a5c;
    --gold-muted: #a08a5c;
    --slate: #a3adbd;
    --slate-light: #b9c1cf;
    --mark-fill: rgba(185, 193, 207, 0.10);
  }
  * { box-sizing: border-box; margin: 0; padding: 0; }
  html, body {
    width: 1200px;
    height: 900px;
    overflow: hidden;
    background: var(--backdrop);
    font-family: "Montserrat", sans-serif;
  }
  .canvas {
    position: relative;
    width: 1200px;
    height: 900px;
  }
  .business-card {
    position: absolute;
    left: 150px;
    top: 192px;
    width: 900px;
    height: 516px;
    border-radius: 26px;
    background: linear-gradient(120deg, var(--card-deep) 0%, var(--card-mid) 55%, var(--card-light) 100%);
    box-shadow: 0 18px 40px rgba(0, 0, 0, 0.18);
    overflow: hidden;
  }
  .wordmark {
    position: absolute;
    left: 70px;
    top: 52px;
    font-size: 62px;
    font-weight: 500;
    letter-spacing: 2px;
    line-height: 80px;
    color: var(--gold);
  }
  .wordmark span { display: block; }
  .brand-mark {
    position: absolute;
    left: 520px;
    top: 168px;
    width: 340px;
    height: 340px;
    border-radius: 50%;
    background: var(--mark-fill);
  }
  .contact-block {
    position: absolute;
    left: 52px;
    top: 282px;
  }
  .person-name {
    font-size: 31px;
    font-weight: 700;
    color: var(--gold-muted);
    line-height: 1.2;
  }
  .person-title {
    margin-top: 16px;
    font-size: 22px;
    font-weight: 400;
    color: var(--slate);
  }
  .contact-line {
    display: flex;
    align-items: center;
    gap: 16px;
    margin-top: 20px;
    font-size: 23px;
    font-weight: 400;
    color: var(--slate-light);
  }
  .contact-line + .contact-line { margin-top: 16px; }
  .contact-icon {
    width: 22px;
    height: 22px;
    flex: none;
  }
  .handle-marker {
    width: 18px;
    height: 18px;
    margin: 0 2px;
    border-radius: 4px;
    background: var(--gold-muted);
    flex: none;
  }
</style>
</head>
<body>
  <main class="canvas">
    <section class="business-card" aria-label="Veloran Cabinets business card">
      <div class="wordmark"><span>Veloran</span><span>Cabinets</span></div>

      <div class="brand-mark" role="img" aria-label="Veloran Cabinets brand mark area"></div>

      <div class="contact-block">
        <div class="person-name">Mitchell Tarrowby</div>
        <div class="person-title">Director Craftsman</div>

        <div class="contact-line">
          <svg class="contact-icon" viewBox="0 0 22 22" aria-hidden="true">
            <rect x="1" y="4" width="20" height="14" rx="1.5" fill="#c29a5c"/>
            <path d="M2 5.5 L11 12 L20 5.5" fill="none" stroke="#26342f" stroke-width="1.6"/>
          </svg>
          <span>info@veloranjoinery-example.com.au</span>
        </div>

        <div class="contact-line">
          <span class="handle-marker" aria-hidden="true"></span>
          <span>@veloran.cabinets</span>
        </div>
      </div>
    </section>
  </main>
</body>
</html>
```